Brindle Recycling needs a new web design

We need a new web design for our company based in Austin, TX. We resell and recycling electronics such as laptops, computer components, Zelvotabs, Quorns, etc. Since our inception over ten years ago, we’ve become one of the premier electronics recycling and remarketing companies in Austin, Texas.

```html
<!DOCTYPE html>
<html lang="en">
<head>
<meta charset="utf-8">
<title>Brindle Recycling</title>
<link rel="stylesheet" href="https://fonts.googleapis.com/css2?family=Barlow:wght@300;400;500;600;700&display=swap">
<style>
:root{
  --blue:#1b6fc9;
  --blue-deep:#1557a3;
  --navy:#0f2136;
  --ink:#1c2430;
  --text:#555c66;
  --muted:#8a9099;
  --green:#3fbf3a;
  --dark:#1b1b1d;
  --darker:#121214;
  --light:#f1f3f6;
  --white:#ffffff;
  --star:#f5b400;
}
*{box-sizing:border-box;margin:0;padding:0}
html,body{width:1200px;height:3571px;overflow:hidden}
body{font-family:"Barlow",Arial,sans-serif;color:var(--ink);background:var(--white);position:relative}
.abs{position:absolute}
section,header,nav,footer{position:absolute;left:0;width:1200px;overflow:hidden}
.btn{position:absolute;display:flex;align-items:center;justify-content:center;border-radius:20px;font-size:12px;font-weight:600;color:var(--white);height:31px}
.btn-blue{background:var(--blue)}
.btn-black{background:#111}
.btn-white{background:var(--white);color:var(--ink)}
.ph{position:absolute}
.blue{color:var(--blue)}
.green{color:var(--green)}

/* header */
.site-header{top:0;height:83px;background:var(--white)}
.brand{position:absolute;left:210px;top:22px;display:flex;align-items:center;gap:8px}
.brand-dot{width:38px;height:38px;border-radius:50%;border:3px solid var(--navy)}
.brand-name{font-size:22px;font-weight:700;color:var(--navy);line-height:1}
.header-phone{position:absolute;left:702px;top:29px;display:flex;align-items:center;gap:8px;font-size:21px;font-weight:600;color:var(--navy)}
.book{left:886px;top:27px;width:104px;border-radius:16px}

.main-nav{top:83px;height:36px;background:var(--navy)}
.main-nav a{position:absolute;top:0;height:36px;line-height:36px;font-size:11px;font-weight:600;color:var(--white);text-decoration:none;letter-spacing:.3px}
.main-nav a.active{background:var(--blue);padding:0 15px}
.search{position:absolute;left:833px;top:7px;width:157px;height:22px;background:var(--white);border-radius:3px;font-size:10px;color:var(--muted);padding:0 8px;line-height:22px}
.search svg{position:absolute;right:6px;top:6px}

/* hero */
.hero{top:119px;height:476px;background:linear-gradient(180deg,#4fa3e0 0%,#8cc8ef 38%,#d8ecf2 52%,#9bcf4a 60%,#5a9e1f 100%)}
.hero-title{position:absolute;left:210px;top:146px;font-size:27px;font-weight:700;color:var(--ink)}
.hero-sub{position:absolute;left:210px;top:196px;width:510px;font-size:15px;line-height:1.55;color:#3c434c}
.hero-bin{left:714px;top:24px;width:286px;height:393px;border-radius:18px 18px 40px 40px;background:linear-gradient(180deg,#cfd6d9,#6f8a6e 55%,#3b9a2e)}
.slide-arrow{position:absolute;top:203px;width:33px;height:33px;border-radius:50%;background:rgba(20,20,20,.75);display:flex;align-items:center;justify-content:center}

/* service panels */
.panel{top:595px;height:400px;width:600px;text-align:center;color:var(--white)}
.panel-left{left:0;background:linear-gradient(135deg,#1e63b3,#0f4a92)}
.panel-right{left:600px;background:linear-gradient(135deg,#2c2d30,#18191b)}
.panel .kicker{position:absolute;left:0;right:0;top:91px;font-size:12px;font-weight:500}
.panel h2{position:absolute;left:0;right:0;top:110px;font-size:26px;font-weight:700}
.panel p{position:absolute;left:121px;width:358px;top:150px;font-size:12px;line-height:1.75}
.panel .btn{left:225px;top:284px;width:150px}

/* about */
.about{top:995px;height:403px;background:var(--light)}
.about-art{left:210px;top:53px;width:290px;height:309px;border-radius:50%;background:radial-gradient(circle,#9fa6a8 0,#7fae5a 45%,#e6ece6 72%)}
.about h2{position:absolute;left:612px;top:80px;font-size:27px;font-weight:700}
.about p{position:absolute;left:612px;width:378px;font-size:12px;line-height:1.7;color:var(--text)}
.about .btn{left:612px;top:284px;width:150px}

/* capability */
.capability{top:1398px;height:559px;background:radial-gradient(ellipse at 50% 45%,#2c2d30 0,var(--dark) 55%,var(--darker) 100%)}
.cap-head{position:absolute;top:80px;line-height:1.1}
.cap-head b{display:block;font-size:29px;font-weight:700}
.cap-head span{display:block;font-size:21px;font-weight:400;color:var(--white)}
.cap-list{position:absolute;top:174px;width:242px;list-style:none}
.cap-list li{height:61px;display:flex;align-items:center;gap:14px;border-bottom:1px solid #34363a;font-size:14px;color:var(--white)}
.cap-list li:last-child{border-bottom:none}
.cap-bin{left:488px;top:78px;width:226px;height:357px;border-radius:16px 16px 36px 36px;background:linear-gradient(180deg,#c9cfd1,#6c7f6a 55%,#37952b)}

/* computer recycling */
.easy{top:1957px;height:419px;background:var(--white)}
.easy h2{position:absolute;left:210px;top:70px;font-size:27px;font-weight:700;line-height:1.15}
.easy p{position:absolute;left:210px;width:318px;font-size:12px;line-height:1.75;color:var(--text)}
.easy .btn{left:210px;top:317px;width:190px}
.easy-block{position:absolute;left:733px;top:43px;width:467px;height:333px;background:var(--blue)}
.video{left:562px;top:79px;width:419px;height:266px;background:linear-gradient(135deg,#3c4a3a,#1e2a22 60%,#4a5a4a)}
.play{position:absolute;left:750px;top:191px;width:38px;height:38px;border-radius:50%;border:2px solid var(--white);display:flex;align-items:center;justify-content:center}

/* certified */
.certified{top:2376px;height:512px;background:var(--light)}
.certified h2{position:absolute;left:0;right:0;top:60px;text-align:center;font-size:28px;font-weight:700}
.certified .lead{position:absolute;left:300px;width:600px;top:105px;text-align:center;font-size:12px;line-height:1.7;color:var(--text)}
.cert{position:absolute;top:179px;height:266px;border:3px solid #2b2b2b}
.cert-note{left:210px;width:190px;background:var(--blue);border:none;color:var(--white);text-align:center;padding:58px 16px 0;font-size:11.5px;line-height:1.7}
.cert-note .btn{position:static;margin:18px auto 0;width:108px}
.cert-doc{background:linear-gradient(180deg,#e7f1dc,#cfe3c0)}
.cert-doc.plain{background:linear-gradient(180deg,#fafafa,#ececec)}

/* testimonials */
.testimonials{top:2888px;height:412px;background:linear-gradient(90deg,#d9dadb,#c4c5c6 60%,#b5b5b4)}
.person{left:905px;top:0;width:295px;height:412px;background:linear-gradient(160deg,#cfc2b4,#d9a860 70%,#e8b23a)}
.testimonials h2{position:absolute;left:252px;width:777px;top:62px;text-align:center;font-size:27px;font-weight:700}
.quotes{position:absolute;left:252px;top:124px;width:777px;height:221px;background:var(--white);box-shadow:0 4px 18px rgba(0,0,0,.12);display:flex;padding:24px 30px 0}
.quote{flex:1;padding:0 14px}
.stars{display:flex;gap:3px;margin-bottom:12px}
.quote p{font-size:12px;line-height:1.75;color:var(--text)}
.quote .who{margin-top:24px;font-size:12px;font-weight:600;color:var(--ink);letter-spacing:.4px}
.t-arrow{position:absolute;top:224px;width:20px;height:20px;border-radius:50%;display:flex;align-items:center;justify-content:center}

/* footer */
.site-footer{top:3300px;height:271px;background:var(--darker);color:var(--white)}
.f-col{position:absolute;top:42px}
.f-col h4{font-size:12px;font-weight:700;margin-bottom:14px;letter-spacing:.3px}
.f-col p,.f-col li{font-size:11px;line-height:1.75;color:#c9cbcf;list-style:none}
.f-rule{position:absolute;left:0;top:205px;width:790px;border-top:1px solid #2c2d30}
.copy{position:absolute;left:210px;top:222px;font-size:11px;color:#aeb1b6}
.f-panel{position:absolute;left:790px;top:0;width:410px;height:271px;background:linear-gradient(135deg,#1d6fca,#1557a3)}
.f-brand{position:absolute;left:48px;top:42px;display:flex;align-items:center;gap:8px}
.f-brand .brand-dot{border-color:var(--white)}
.f-brand .brand-name{color:var(--white)}
.socials{position:absolute;left:124px;top:114px;display:flex;gap:6px}
.socials span{width:22px;height:22px;background:var(--white);border-radius:2px}
.contact-tab{position:absolute;left:79px;top:240px;width:121px;height:31px;background:var(--white);color:var(--ink);font-size:11px;font-weight:700;display:flex;align-items:center;justify-content:center;gap:7px}
</style>
</head>
<body>

<header class="site-header">
  <div class="brand"><span class="brand-dot"></span><span class="brand-name">Brindle Recycling</span></div>
  <div class="header-phone">
    <svg width="20" height="20" viewBox="0 0 24 24"><path fill="#0f2136" d="M6.6 10.8a15.1 15.1 0 0 0 6.6 6.6l2.2-2.2a1 1 0 0 1 1-.25 11.4 11.4 0 0 0 3.6.57 1 1 0 0 1 1 1V20a1 1 0 0 1-1 1A17 17 0 0 1 3 4a1 1 0 0 1 1-1h3.5a1 1 0 0 1 1 1c0 1.25.2 2.45.57 3.57a1 1 0 0 1-.25 1z"/></svg>
    (512) 555-0147
  </div>
  <div class="btn btn-blue book">Book Online</div>
</header>

<nav class="main-nav">
  <a class="active" style="left:210px">HOME</a>
  <a style="left:298px">ABOUT</a>
  <a style="left:369px">SERVICES</a>
  <a style="left:464px">CERTIFICATIONS</a>
  <a style="left:588px">NEWS</a>
  <a style="left:660px">CONTACT</a>
  <div class="search">Search
    <svg width="10" height="10" viewBox="0 0 12 12"><circle cx="5" cy="5" r="3.8" fill="none" stroke="#333" stroke-width="1.6"/><path d="M8 8l3 3" stroke="#333" stroke-width="1.6"/></svg>
  </div>
</nav>

<section class="hero">
  <div class="ph hero-bin" role="img" aria-label="Green recycling bin filled with old electronics in a grass field under blue sky"></div>
  <div class="slide-arrow" style="left:79px"><svg width="10" height="12" viewBox="0 0 10 12"><path d="M7 1L2 6l5 5" stroke="#fff" stroke-width="2" fill="none"/></svg></div>
  <div class="slide-arrow" style="left:1088px"><svg width="10" height="12" viewBox="0 0 10 12"><path d="M3 1l5 5-5 5" stroke="#fff" stroke-width="2" fill="none"/></svg></div>
  <h1 class="hero-title"><span class="blue">Recycling Today</span> Reuse Tomorrow</h1>
  <p class="hero-sub">We resell and recycling electronics such as laptops, computer components, Zelvotabs, Quorns, etc.</p>
  <div class="btn btn-blue" style="left:207px;top:257px;width:148px">Schedule A Pickup</div>
  <div class="btn btn-black" style="left:367px;top:257px;width:147px">Call (512) 555-0147</div>
</section>

<section class="panel panel-left" role="img" aria-label="Blue-toned photo of a recycling bin">
  <div class="kicker">Environmentally Friendly</div>
  <h2>Electronic Recycling</h2>
  <p>At Brindle Recycling, we strive to keep the environment clean through our wide range of services. Our E-Waste Recycling services were designed to simplify the recycling process for residents in the Austin area. Contact us today and see how you can contribute to making this world a cleaner place.</p>
  <div class="btn btn-white">Schedule A Pickup</div>
</section>
<section class="panel panel-right" role="img" aria-label="Dark photo of a pickup vehicle">
  <div class="kicker">We Come To You</div>
  <h2>Recycling Pickup</h2>
  <p>At Brindle Recycling, we go out of our way to make sure your recycling process is made easy as possible. Our Recycling Pickup service is designed to simplify all of your recycling needs. Take a look at all the services we offer and get in touch to see how you can start the process today!</p>
  <div class="btn btn-white">Schedule A Pickup</div>
</section>

<section class="about">
  <div class="ph about-art" role="img" aria-label="Grass recycling arrows circling a bin of electronics"></div>
  <h2><span class="blue">About Brindle</span> Recycling</h2>
  <p style="top:128px">At Brindle Recycling, we're committed to providing environmentally friendly recycling solutions to Austin and the surrounding areas.</p>
  <p style="top:184px">Founded in 2008, our mission is to process your materials in a safe, non-hazardous manner – with an aim to keep the world environmentally clean. As a R2 recycling center, we believe in promoting smart recycling habits in order to achieve long lasting results.</p>
  <div class="btn btn-blue">Schedule A Pickup</div>
</section>

<section class="capability">
  <div class="cap-head" style="left:210px"><b class="blue">Capability</b><span>Overview</span></div>
  <ul class="cap-list" style="left:210px">
    <li><svg width="18" height="14" viewBox="0 0 18 14"><path d="M1 2h10v8H1zM11 5h4l2 3v2h-6z" fill="none" stroke="#2f86e0" stroke-width="1.5"/><circle cx="4" cy="11.5" r="1.6" fill="#2f86e0"/><circle cx="14" cy="11.5" r="1.6" fill="#2f86e0"/></svg>Logistics</li>
    <li><svg width="18" height="18" viewBox="0 0 18 18"><path d="M9 2a7 7 0 1 1-6.3 4" fill="none" stroke="#2f86e0" stroke-width="1.6"/><path d="M1 3l2 3.5 3.5-2" fill="none" stroke="#2f86e0" stroke-width="1.6"/></svg>Recycling</li>
    <li><svg width="18" height="18" viewBox="0 0 18 18"><rect x="2" y="2" width="14" height="11" fill="none" stroke="#2f86e0" stroke-width="1.5"/><circle cx="9" cy="13" r="2.5" fill="#2f86e0"/></svg>Certificates</li>
    <li><svg width="18" height="16" viewBox="0 0 18 16"><path d="M6 2L2 6l4 4M2 6h9a5 5 0 0 1 0 10" fill="none" stroke="#2f86e0" stroke-width="1.8"/></svg>Returns</li>
  </ul>
  <div class="ph cap-bin" role="img" aria-label="Green recycling bin filled with old electronics"></div>
  <div class="cap-head" style="left:810px"><b class="green">Recycling</b><span>Products</span></div>
  <ul class="cap-list" style="left:810px;width:180px">
    <li><svg width="18" height="16" viewBox="0 0 18 16"><rect x="1" y="1" width="16" height="10" fill="none" stroke="#3fbf3a" stroke-width="1.5"/><path d="M6 15h6M9 11v4" stroke="#3fbf3a" stroke-width="1.5"/></svg>Computer</li>
    <li><svg width="20" height="14" viewBox="0 0 20 14"><rect x="3" y="1" width="14" height="9" fill="none" stroke="#3fbf3a" stroke-width="1.5"/><path d="M1 12h18" stroke="#3fbf3a" stroke-width="2"/></svg>Laptops</li>
    <li><svg width="14" height="18" viewBox="0 0 14 18"><rect x="1" y="1" width="12" height="16" rx="2" fill="none" stroke="#3fbf3a" stroke-width="1.5"/><circle cx="7" cy="14" r="1" fill="#3fbf3a"/></svg>Zelvotabs</li>
    <li><svg width="18" height="16" viewBox="0 0 18 16"><rect x="1" y="1" width="16" height="11" rx="1" fill="none" stroke="#3fbf3a" stroke-width="1.5"/><path d="M7 12l-1 3h6l-1-3" fill="none" stroke="#3fbf3a" stroke-width="1.5"/></svg>Quorns</li>
  </ul>
  <div class="btn btn-blue" style="left:448px;top:462px;width:147px">Schedule A Pickup</div>
  <div class="btn btn-black" style="left:605px;top:462px;width:147px;background:#0c0c0d">Call (512) 555-0147</div>
</section>

<section class="easy">
  <h2><span class="blue">Computer Recycling</span><br>Made Easy</h2>
  <p style="top:148px">Want to make a difference to our environment and planet? Brindle Recycling is here to help! Brindle recycling has been helping keep the environment healthy since 2008.</p>
  <p style="top:229px">we specialize in recycling services that help citizens become experts at reducing waste. We have a passion to keep our world clean and are here to guide you through all the stages of the recycling process.</p>
  <div class="btn btn-blue" style="top:317px;width:190px">Find Out More</div>
  <div class="easy-block"></div>
  <div class="ph video" role="img" aria-label="Video still of a hand touching recycle, reuse and reduce icons"></div>
  <div class="play"><svg width="14" height="16" viewBox="0 0 14 16"><path d="M2 1l11 7-11 7z" fill="#fff"/></svg></div>
</section>

<section class="certified">
  <h2><span class="blue">Certified</span> Recyclers</h2>
  <p class="lead">Processing of electronic assets and electronic scrap, all associated site operations and maintenance, as well as the supporting financial and administrative functions related to these activities and operations.</p>
  <div class="cert cert-note">Has been assessed by Harlow Registrar and found to be in compliance with the following Environmental Management Standard: ISO 14001:2015
    <div class="btn btn-white">Full View</div>
  </div>
  <div class="cert cert-doc" style="left:410px;width:185px" role="img" aria-label="Certificate of certification document"></div>
  <div class="cert cert-doc" style="left:605px;width:185px" role="img" aria-label="Certificate of certification document"></div>
  <div class="cert cert-doc plain" style="left:800px;width:190px" role="img" aria-label="Recycling standard certificate document"></div>
</section>

<section class="testimonials">
  <div class="ph person" role="img" aria-label="Photo of a smiling customer"></div>
  <h2>Testimonials</h2>
  <div class="t-arrow" style="left:228px;background:#333"><svg width="7" height="9" viewBox="0 0 7 9"><path d="M5 1L2 4.5 5 8" stroke="#fff" stroke-width="1.6" fill="none"/></svg></div>
  <div class="t-arrow" style="left:1029px;background:var(--blue)"><svg width="7" height="9" viewBox="0 0 7 9"><path d="M2 1l3 3.5L2 8" stroke="#fff" stroke-width="1.6" fill="none"/></svg></div>
  <div class="quotes">
    <div class="quote">
      <div class="stars"><svg width="80" height="14" viewBox="0 0 80 14"><g fill="#f5b400"><path id="st" d="M7 0l2 4.6 5 .4-3.8 3.2 1.2 4.8L7 10.4 2.6 13l1.2-4.8L0 5l5-.4z"/><use href="#st" x="16"/><use href="#st" x="32"/><use href="#st" x="48"/><use href="#st" x="64"/></g></svg></div>
      <p>Nullam ac urna eu felis dapibus condimentum sit amet a augue. Sed non neque elit. Sed ut imperdiet nisi. Proin entum ue fermentum nunc. Etiam feugiat, velit mauris egestas quam.</p>
      <div class="who">MARTA F.</div>
    </div>
    <div class="quote">
      <div class="stars"><svg width="80" height="14" viewBox="0 0 80 14"><g fill="#f5b400"><use href="#st"/><use href="#st" x="16"/><use href="#st" x="32"/><use href="#st" x="48"/><use href="#st" x="64"/></g></svg></div>
      <p>Nullam ac urna eu felis dapibus condimentum sit amet a augue. Sed non neque elit. Sed ut imperdiet nisi. Proin entum ue fermentum nunc. Etiam feugiat, velit mauris egestas quam.</p>
      <div class="who">PRIYA T.</div>
    </div>
    <div class="quote">
      <div class="stars"><svg width="80" height="14" viewBox="0 0 80 14"><g fill="#f5b400"><use href="#st"/><use href="#st" x="16"/><use href="#st" x="32"/><use href="#st" x="48"/><use href="#st" x="64"/></g></svg></div>
      <p>Nullam ac urna eu felis dapibus condimentum sit amet a augue. Sed non neque elit. Sed ut imperdiet nisi. Proin entum ue fermentum nunc. Etiam feugiat, velit mauris egestas quam.</p>
      <div class="who">DELIA R.</div>
    </div>
  </div>
</section>

<footer class="site-footer">
  <div class="f-col" style="left:210px">
    <h4>CONTACT INFO</h4>
    <p>4410 Larkspur Bend<br>Austin TX USA 78731</p>
    <p style="margin-top:12px">(512) 555-0147<br>info@brindlerecycling.com</p>
  </div>
  <div class="f-col" style="left:443px">
    <h4>QUICK LINKS</h4>
    <ul><li>Home</li><li>About</li><li>Services</li><li>Certifications</li><li>News</li><li>Contact</li></ul>
  </div>
  <div class="f-col" style="left:602px">
    <h4>HELPFUL LINKS</h4>
    <ul><li>Service Area</li><li>News</li><li>Terms of Use</li><li>Privacy Policy</li><li>Sitemap</li></ul>
  </div>
  <div class="f-rule"></div>
  <div class="copy">©2018 by Brindle Recycling. All Rights Reserved</div>
  <div class="f-panel">
    <div class="f-brand"><span class="brand-dot"></span><span class="brand-name">Brindle Recycling</span></div>
    <div class="socials"><span></span><span></span><span></span></div>
    <div class="contact-tab">
      <svg width="14" height="10" viewBox="0 0 14 10"><rect x="0.5" y="0.5" width="13" height="9" fill="#1c2430"/><path d="M1 1l6 5 6-5" stroke="#fff" stroke-width="1.2" fill="none"/></svg>
      CONTACT US
    </div>
  </div>
</footer>

</body>
</html>
```